Ridgeway Mining Solutions Business Card

Ridgeway Mining Solutions is a company that provides consulting services to the Mining Industry.

Whilst Ridgeway Mining Solutions is an Australian based company its client base is the global mining industry.

The essence of Ridgeway Mining Solutions is its a can do organisation that can make a difference to its clients by providing quality assistance and form lasting relationships.
Updates

Target Market(s)

The global Mining Industry.

Industry/Entity Type

Mining

Font styles to use
Serif

Colors

Designer to choose colors to be used in the design.

Requirements
Nice to have
• My thinking is the card would look good in black given the logo.

I would like to see written on the back side of the card " Providing Metallurgical, Management and Corporate Services to the Mining Industry"

```html
<!DOCTYPE html>
<html lang="en">
<head>
<meta charset="utf-8">
<title>Ridgeway Mining Solutions Business Card</title>
<link href="https://fonts.googleapis.com/css2?family=Tinos:wght@400;700&display=swap" rel="stylesheet">
<style>
  :root {
    --backdrop: #d9d9d9;
    --card: #0c0c0c;
    --gold: #f0a526;
    --ink: #e8e8e8;
    --muted: #a9a9a9;
    --frame: #cfcfcf;
  }
  * { margin: 0; padding: 0; box-sizing: border-box; }
  html, body { width: 1200px; height: 803px; overflow: hidden; }
  body {
    background: var(--backdrop);
    font-family: "Tinos", "Times New Roman", serif;
    position: relative;
  }
  .card {
    position: absolute;
    top: 62px;
    width: 400px;
    height: 680px;
    background: var(--card);
    box-shadow: 0 10px 30px rgba(0,0,0,0.35);
  }
  .card--front { left: 170px; }
  .card--back { left: 630px; }

  .wordmark {
    color: var(--gold);
    font-weight: 700;
    text-transform: uppercase;
    text-align: center;
    line-height: 1.05;
    letter-spacing: 2px;
  }
  .wordmark__name { display: block; font-size: 52px; letter-spacing: 3px; }
  .wordmark__sub { display: block; font-size: 20px; letter-spacing: 6px; margin-top: 6px; }

  .card--front .wordmark { position: absolute; left: 0; right: 0; top: 430px; }
  .tagline {
    position: absolute; left: 30px; right: 30px; top: 560px;
    text-align: center; color: var(--muted); font-size: 17px;
  }

  .card--back .wordmark { position: absolute; left: 0; right: 0; top: 70px; }
  .contact-frame {
    position: absolute; left: 30px; right: 30px; top: 230px; bottom: 40px;
    border: 1.5px solid var(--frame);
    border-radius: 42px;
    padding: 28px 30px 0;
  }
  .person { text-align: center; margin-bottom: 22px; }
  .person__name { color: var(--ink); font-size: 24px; letter-spacing: 2px; text-transform: uppercase; }
  .person__role { color: var(--ink); font-size: 15px; margin-top: 2px; }
  .contact-list { list-style: none; }
  .contact-row {
    display: flex; align-items: flex-start; gap: 18px;
    padding: 14px 0 14px;
    border-bottom: 2px solid var(--gold);
    color: var(--ink); font-size: 21px; line-height: 1.25;
  }
  .contact-row:last-child { border-bottom: none; }
  .contact-row svg { flex: 0 0 26px; width: 26px; height: 26px; fill: var(--gold); stroke: var(--gold); }
</style>
</head>
<body>
  <section class="card card--front" aria-label="Card front">
    <div class="wordmark">
      <span class="wordmark__name">Ridgeway</span>
      <span class="wordmark__sub">Mining Solutions</span>
    </div>
    <p class="tagline">We provide consulting services to the Mining Industry..</p>
  </section>

  <section class="card card--back" aria-label="Card back">
    <div class="wordmark">
      <span class="wordmark__name">Ridgeway</span>
      <span class="wordmark__sub">Mining Solutions</span>
    </div>
    <div class="contact-frame">
      <div class="person">
        <p class="person__name">Marcus Hale</p>
        <p class="person__role">Managing Director</p>
      </div>
      <ul class="contact-list">
        <li class="contact-row">
          <svg viewBox="0 0 24 24" aria-hidden="true"><path stroke="none" d="M3 9c0-3 4-5 9-5s9 2 9 5v2h-5V9H8v2H3z M6 12h12l2 8H4z"/></svg>
          <span>0061 2480 3157</span>
        </li>
        <li class="contact-row">
          <svg viewBox="0 0 24 24" aria-hidden="true"><rect x="2" y="5" width="20" height="14" stroke="none"/><path d="M2 5l10 8 10-8" fill="none" stroke="#0c0c0c" stroke-width="1.5"/></svg>
          <span>info@ridgewaymining.com</span>
        </li>
        <li class="contact-row">
          <svg viewBox="0 0 24 24" aria-hidden="true"><rect x="3" y="4" width="18" height="12" fill="none" stroke-width="2"/><path stroke="none" d="M9 18h6v2H9z"/></svg>
          <span>www.ridgewaymining.com</span>
        </li>
        <li class="contact-row">
          <svg viewBox="0 0 24 24" aria-hidden="true"><path stroke="none" d="M12 3l10 9h-3v9h-5v-6h-4v6H5v-9H2z"/></svg>
          <span>Ridgeway House 120<br>Quarry Rd, Perth WA 6000</span>
        </li>
      </ul>
    </div>
  </section>
</body>
</html>
```